Business Card Design Project

Lorabelle is a women fashion house focusing on youthful glamour.

We bring together unique designs, premium quality materials and top craftsmanship to deliver sophisticated yet playful glamour, fun and excitement to the confident woman.

We can sum up the brand identity in 3 words:
Glamour – Sophistication – Unique

Industry/Entity Type

Fashion

Requirements
Must have
• Nim Ferrasco
nim.ferrasco@lorabelle-example.com
Mobile: 081 536 2947
Instragram: lorabelle_label
Facebook: lorabelle

Creative Director
Lorabelle Co., LTD
TEL: 02 631 48 97
42 Maple Row, 2nd Floor , D Building , Thonrak , Chaloemrat 28.
East Sanphet , Rattana , Bangkok 10240 Thailand
www.lorabelle-example.com

```html
<!DOCTYPE html>
<html lang="en">
<head>
<meta charset="utf-8">
<title>Lorabelle – Business Card</title>
<link rel="stylesheet" href="https://fonts.googleapis.com/css2?family=Playfair+Display:wght@400&family=Roboto:wght@400;500&display=swap">
<style>
  :root {
    --backdrop: #d8d3cb;
    --card: #0b0b0b;
    --card-edge: #1c1c1c;
    --ink: #f2f2f2;
    --ink-soft: #d6d6d6;
    --rule: rgba(255,255,255,0.75);
  }
  * { margin: 0; padding: 0; box-sizing: border-box; }
  html, body {
    width: 1200px; height: 1000px; overflow: hidden;
    background: var(--backdrop);
  }
  .stage {
    width: 1200px; height: 1000px;
    display: flex; align-items: center; justify-content: center;
  }
  .business-card {
    position: relative;
    width: 480px; height: 840px;
    background: var(--card);
    border: 1px solid var(--card-edge);
    border-radius: 4px;
    box-shadow: 0 18px 40px rgba(0,0,0,0.35);
    overflow: hidden;
    color: var(--ink);
    font-family: "Roboto", Arial, sans-serif;
  }
  .card-sheen {
    position: absolute; inset: 0;
    background: linear-gradient(125deg, rgba(255,255,255,0) 30%, rgba(255,255,255,0.09) 48%, rgba(255,255,255,0.02) 62%, rgba(255,255,255,0) 75%);
    pointer-events: none;
  }
  .brand {
    position: absolute; top: 78px; left: 0; right: 0;
    text-align: center;
  }
  .brand-name {
    font-family: "Playfair Display", Georgia, serif;
    font-weight: 400;
    font-size: 80px;
    line-height: 1;
    color: var(--ink);
  }
  .brand-rule {
    position: absolute; top: 212px; left: 90px;
    width: 300px; height: 1px;
    background: linear-gradient(90deg, rgba(255,255,255,0), var(--rule) 50%, rgba(255,255,255,0));
  }
  .person {
    position: absolute; top: 278px; left: 85px;
  }
  .person-name { font-size: 26px; font-weight: 500; }
  .person-title { font-size: 17px; margin-top: 6px; color: var(--ink-soft); }
  .person-company { font-size: 17px; margin-top: 4px; color: var(--ink-soft); }
  .contact-list {
    position: absolute; top: 390px; left: 44px; right: 20px;
    list-style: none;
  }
  .contact-item {
    display: flex; align-items: center;
    height: 38px;
    font-size: 18px;
    color: var(--ink-soft);
    white-space: nowrap;
  }
  .contact-icon {
    width: 24px; height: 20px; margin-right: 17px;
    display: flex; align-items: center; justify-content: center;
    flex-shrink: 0;
  }
  .contact-icon svg { fill: none; stroke: var(--ink-soft); stroke-width: 1.6; }
  .contact-icon .solid { fill: var(--ink-soft); stroke: none; }
  .address { margin-top: 4px; font-size: 18px; color: var(--ink-soft); line-height: 34px; }
  .address-first { display: flex; align-items: center; }
</style>
</head>
<body>
<main class="stage">
  <article class="business-card">
    <div class="card-sheen"></div>

    <header class="brand">
      <div class="brand-name">Lorabelle</div>
    </header>
    <div class="brand-rule"></div>

    <section class="person">
      <div class="person-name">Nim Ferrasco</div>
      <div class="person-title">Creative Director</div>
      <div class="person-company">Lorabelle Co., LTD</div>
    </section>

    <ul class="contact-list">
      <li class="contact-item">
        <span class="contact-icon">
          <svg width="22" height="16" viewBox="0 0 22 16"><rect x="1" y="1" width="20" height="14" rx="1"/><path d="M1 1 L11 9 L21 1"/></svg>
        </span>
        nim.ferrasco@lorabelle-example.com
      </li>
      <li class="contact-item">
        <span class="contact-icon">
          <svg width="14" height="20" viewBox="0 0 14 20"><rect x="1" y="1" width="12" height="18" rx="2"/><circle class="solid" cx="7" cy="16" r="1.2"/></svg>
        </span>
        081 536 2947
      </li>
      <li class="contact-item">
        <span class="contact-icon">
          <svg width="18" height="18" viewBox="0 0 18 18"><path class="solid" d="M4 1 L7 5 L5 7.5 C6 10 8 12 10.5 13 L13 11 L17 14 L15 17 C8 17 1 10 1 3 Z"/></svg>
        </span>
        02 631 48 97
      </li>
      <li class="contact-item">
        <span class="contact-icon">
          <svg width="18" height="18" viewBox="0 0 18 18"><rect x="1" y="1" width="16" height="16" rx="4"/></svg>
        </span>
        lorabelle_label
      </li>
      <li class="contact-item">
        <span class="contact-icon">
          <svg width="18" height="18" viewBox="0 0 18 18"><rect x="1" y="1" width="16" height="16" rx="1"/></svg>
        </span>
        lorabelle
      </li>
      <li class="contact-item">
        <span class="contact-icon">
          <svg width="18" height="18" viewBox="0 0 18 18"><circle cx="9" cy="9" r="8"/></svg>
        </span>
        www.lorabelle-example.com
      </li>
      <li class="address">
        <div class="address-first">
          <span class="contact-icon">
            <svg width="16" height="20" viewBox="0 0 16 20"><path class="solid" d="M8 0 C3.6 0 0 3.4 0 7.6 C0 13 8 20 8 20 C8 20 16 13 16 7.6 C16 3.4 12.4 0 8 0 Z"/><circle cx="8" cy="7.5" r="2.6" fill="#0b0b0b" stroke="none"/></svg>
          </span>
          42 Maple Row, 2nd Floor , D Building ,
        </div>
        <div class="address-line">Thonrak , Chaloemrat 28.</div>
        <div class="address-line">East Sanphet , Rattana , Bangkok</div>
        <div class="address-line">10240 Thailand</div>
      </li>
    </ul>
  </article>
</main>
</body>
</html>
```